Fire Risk Assessment App needs a sleek UI design

I need a sleek, modern but professional design for my 5 page Fire Risk Assessment App. Include gradient background, fire themed colours including reds, yellows, light orange and a touch of black. Design must ooze simplicity and professionalism. This is for the UK market. See attached images and word doc for more information.

Target Market(s)

General public and business owners

Industry/Entity Type

Technology / Fire Safety

Colors
00AB8E
00BBA5
67D7C9
C6EFE9
E9F9F6
59FF00
82FF00
B8FF75
E3FFCB
F4FFEA
FFC000
F8CF3A
FAE287
FDF2CF
FEFAEE
F0912C
F2A743
F7CA91
FBE8D2
FDF5EE
EE7325
F08F49
F5BC92
FAE3D3
FDF4ED
EB3D1F
EC4F4E
F09395
F8D3D4
FCEDEE

```html
<!DOCTYPE html>
<html lang="en">
<head>
<meta charset="utf-8">
<title>Fire Risk Assessment App – UI Screens</title>
<link href="https://fonts.googleapis.com/css2?family=Montserrat:wght@400;500;600;700&display=swap" rel="stylesheet">
<style>
  :root{
    --stage:#666666;
    --bar:#3d3d3d;
    --fire-top:#ffb400;
    --fire-mid:#ff8c0c;
    --fire-low:#ff5d16;
    --flame-red:#eb3d1f;
    --ink:#1a1a1a;
    --white:#ffffff;
    --tick:#4caf50;
    --amber:#ffc000;
    --chat:#f0912c;
  }
  *{box-sizing:border-box;margin:0;padding:0}
  html,body{width:1200px;height:848px;overflow:hidden;background:var(--stage);font-family:"Montserrat",sans-serif}
  .stage{position:relative;width:1200px;height:848px}
  .screen{position:absolute;top:46px;width:349px;height:755px;overflow:hidden;
    background:linear-gradient(180deg,var(--fire-top) 0%,var(--fire-mid) 45%,var(--fire-low) 100%);color:var(--white)}
  .screen--welcome{left:42px}
  .screen--dashboard{left:426px}
  .screen--support{left:809px}
  .abs{position:absolute}
  .center-x{left:0;right:0;text-align:center}

  .app-bar{position:absolute;left:0;top:0;width:100%;height:50px;background:var(--bar);
    display:flex;align-items:center;justify-content:center;gap:10px;font-weight:700;font-size:18px}
  .app-bar svg{width:36px;height:28px}

  /* welcome */
  .tagline{top:14px;color:var(--ink);font-weight:600;font-size:17.5px;line-height:22px}
  .preview-art{left:62px;top:80px;width:210px;height:280px;border-radius:6px;transform:rotate(-8deg);
    background:linear-gradient(170deg,#ffffff 0%,#f6f1ec 70%,#d9534a 100%)}
  .field{left:21px;top:388px;width:307px;height:34px;border:1.5px solid var(--white);border-radius:8px;
    display:flex;align-items:center;justify-content:space-between;padding:0 9px;font-size:13px}
  .field svg{width:20px;height:20px}
  .btn{left:74px;width:201px;height:46px;background:var(--white);color:var(--ink);border-radius:2px;
    display:flex;align-items:center;justify-content:center;gap:14px;font-size:12.5px;font-weight:500}
  .btn svg{width:26px;height:26px}
  .btn--create{top:445px}
  .btn--login{top:548px}
  .note{font-size:15.5px;line-height:22px}
  .fingerprint{left:147px;top:663px;width:56px;height:74px}

  /* dashboard */
  .fra-badge{left:145px;top:80px;width:62px;height:62px}
  .label{font-weight:500;font-size:13.5px;color:var(--ink)}
  .type-tile{width:60px;height:60px;border-radius:50%;background:var(--white);display:flex;align-items:center;justify-content:center}
  .type-tile svg{width:40px;height:36px}
  .section-tab{left:20px;width:189px;height:34px;border:1.5px solid var(--white);display:flex;align-items:center;
    justify-content:space-between;padding:0 10px;font-size:14.5px;font-weight:500}
  .section-tab svg{width:20px;height:20px}
  .site-row{left:20px;display:flex;align-items:center;gap:10px;font-size:13px;font-weight:500}
  .ring{width:19px;height:19px;border:1.6px solid var(--white);border-radius:50%}
  .site-chip{width:46px;height:46px;border-radius:50%;background:var(--white);display:flex;align-items:center;justify-content:center}
  .site-chip svg{width:32px;height:28px}
  .tab-bar{position:absolute;left:0;bottom:0;width:100%;height:47px;background:var(--white);display:flex;align-items:center}
  .tab-bar .tab{flex:1;display:flex;align-items:center;justify-content:center;height:30px;border-left:1px solid #333}
  .tab-bar .tab:first-child{border-left:none}
  .tab-bar svg{width:34px;height:28px}

  /* support */
  .prompt{left:20px;top:86px;right:20px;display:flex;justify-content:space-between;align-items:center;font-size:15.5px}
  .prompt svg{width:20px;height:20px}
  .reply-box{left:21px;top:115px;width:307px;height:104px;border:1.5px solid var(--white);border-radius:8px}
  .send{left:220px;top:238px;width:108px;height:41px;background:var(--white);color:var(--ink);
    display:flex;align-items:center;justify-content:center;gap:18px;font-size:13px}
  .send svg{width:30px;height:28px}
</style>
</head>
<body>
<svg width="0" height="0" style="position:absolute">
  <defs>
    <symbol id="ico-gauge" viewBox="0 0 40 26">
      <path d="M3 24a17 17 0 0 1 34 0" fill="none" stroke="#fff" stroke-width="6"/>
      <path d="M3 24a17 17 0 0 1 5-12" fill="none" stroke="#eb3d1f" stroke-width="5"/>
      <path d="M8 12a17 17 0 0 1 12-5" fill="none" stroke="#ffc000" stroke-width="5"/>
      <path d="M20 7a17 17 0 0 1 12 5" fill="none" stroke="#f0912c" stroke-width="5"/>
      <path d="M32 12a17 17 0 0 1 5 12" fill="none" stroke="#4caf50" stroke-width="5"/>
      <path d="M20 23L31 15" stroke="#222" stroke-width="3" stroke-linecap="round"/>
      <circle cx="20" cy="23" r="2.5" fill="#222"/>
    </symbol>
    <symbol id="ico-gauge-dark" viewBox="0 0 40 26">
      <path d="M4 24a16 16 0 0 1 32 0" fill="none" stroke="#111" stroke-width="7"/>
      <path d="M20 23L30 16" stroke="#111" stroke-width="3" stroke-linecap="round"/>
    </symbol>
    <symbol id="ico-wallet" viewBox="0 0 40 30">
      <path d="M10 8L26 2l3 6" fill="#111"/>
      <rect x="4" y="8" width="32" height="20" rx="2" fill="#111"/>
      <rect x="8" y="19" width="4" height="3" fill="#fff"/><rect x="14" y="19" width="4" height="3" fill="#fff"/>
      <rect x="20" y="19" width="4" height="3" fill="#fff"/><rect x="26" y="19" width="4" height="3" fill="#fff"/>
      <rect x="8" y="12" width="9" height="4" fill="#fff"/>
    </symbol>
    <symbol id="ico-chat" viewBox="0 0 40 30">
      <path d="M6 2h28a4 4 0 0 1 4 4v14a4 4 0 0 1-4 4H17l-8 6v-6H6a4 4 0 0 1-4-4V6a4 4 0 0 1 4-4z"/>
      <circle cx="14" cy="13" r="2" fill="#fff"/><circle cx="20" cy="13" r="2" fill="#fff"/><circle cx="26" cy="13" r="2" fill="#fff"/>
    </symbol>
    <symbol id="ico-exit" viewBox="0 0 40 30">
      <rect x="18" y="3" width="16" height="25" fill="none" stroke="#111" stroke-width="2.5"/>
      <path d="M6 16h14M15 11l5 5-5 5" fill="none" stroke="#111" stroke-width="3"/>
      <circle cx="9" cy="25" r="4" fill="#111"/>
    </symbol>
    <symbol id="ico-mic" viewBox="0 0 24 24">
      <rect x="9" y="3" width="6" height="11" rx="3" fill="none" stroke="#fff" stroke-width="1.6"/>
      <path d="M6 11a6 6 0 0 0 12 0M12 17v4M9 21h6M3 8v4M21 8v4" fill="none" stroke="#fff" stroke-width="1.6"/>
    </symbol>
    <symbol id="ico-pie" viewBox="0 0 24 24">
      <circle cx="12" cy="12" r="10" fill="#fff"/>
      <path d="M12 12V2a10 10 0 0 1 10 10z" fill="#ff9a10"/>
      <path d="M12 12h10a10 10 0 0 1-3 7z" fill="#ff9a10" opacity=".6"/>
    </symbol>
    <symbol id="ico-building" viewBox="0 0 40 34">
      <rect x="4" y="8" width="32" height="24" fill="#111"/>
      <rect x="10" y="2" width="20" height="7" fill="#111"/>
      <g fill="#fff">
        <rect x="8" y="12" width="3" height="4"/><rect x="14" y="12" width="3" height="4"/><rect x="23" y="12" width="3" height="4"/><rect x="29" y="12" width="3" height="4"/>
        <rect x="8" y="20" width="3" height="4"/><rect x="14" y="20" width="3" height="4"/><rect x="23" y="20" width="3" height="4"/><rect x="29" y="20" width="3" height="4"/>
        <rect x="18" y="24" width="4" height="8"/>
      </g>
    </symbol>
    <symbol id="ico-house" viewBox="0 0 40 36">
      <path d="M20 2L2 16h5v18h26V16h5z" fill="#111"/>
      <g fill="#fff"><rect x="11" y="19" width="3" height="11"/><rect x="16" y="19" width="3" height="11"/><rect x="21" y="19" width="3" height="11"/><rect x="26" y="19" width="3" height="11"/><circle cx="20" cy="13" r="2"/></g>
    </symbol>
  </defs>
</svg>

<main class="stage">

  <section class="screen screen--welcome">
    <h1 class="abs center-x tagline">The most user friendly'<br>Fire Risk Assessment App available.</h1>
    <div class="abs preview-art" role="img" aria-label="Illustration of stacked assessment question cards with a fire extinguisher photo"></div>
    <div class="abs field"><span>Lorem i |</span><svg><use href="#ico-mic"/></svg></div>
    <a class="abs btn btn--create">
      <svg viewBox="0 0 26 26"><circle cx="11" cy="7" r="5" fill="#111"/><path d="M2 24a9 9 0 0 1 18 0z" fill="#111"/><circle cx="20" cy="19" r="5" fill="#111" stroke="#fff" stroke-width="1.5"/><path d="M20 16.5v5M17.5 19h5" stroke="#fff" stroke-width="1.5"/></svg>
      Create a Free account
    </a>
    <p class="abs center-x note" style="top:503px">Any Responsible Person can do it.</p>
    <a class="abs btn btn--login">
      <svg viewBox="0 0 26 26"><circle cx="11" cy="7" r="5" fill="#111"/><path d="M2 24a9 9 0 0 1 18 0z" fill="#111"/><rect x="16" y="16" width="9" height="8" fill="#111" stroke="#fff" stroke-width="1"/><path d="M18 16v-2a2.5 2.5 0 0 1 5 0v2" fill="none" stroke="#111" stroke-width="1.6"/></svg>
      Customer Log In
    </a>
    <p class="abs center-x note" style="top:608px">Created and endorsed by<br>British Firefighters.</p>
    <svg class="abs fingerprint" viewBox="0 0 56 74" fill="none" stroke="#111" stroke-width="3" stroke-linecap="round">
      <path d="M8 20a24 24 0 0 1 40 0"/>
      <path d="M4 36a24 24 0 0 1 48 0v10"/>
      <path d="M10 50V36a18 18 0 0 1 36 0v16a10 10 0 0 1-6 9"/>
      <path d="M16 58V36a12 12 0 0 1 24 0v18"/>
      <path d="M22 66V36a6 6 0 0 1 12 0v22a14 14 0 0 1-4 10"/>
      <path d="M28 40v28"/>
    </svg>
  </section>

  <section class="screen screen--dashboard">
    <header class="app-bar"><svg><use href="#ico-gauge"/></svg>Dashboard</header>
    <svg class="abs fra-badge" viewBox="0 0 62 62">
      <circle cx="30" cy="30" r="30" fill="var(--flame-red)"/>
      <path d="M24 14h12v10h10v12H36v10H24V36H14V24h10z" fill="#fff"/>
      <path d="M50 40v10h8l-2 10h-8l-3-6v-8z" fill="#fff" stroke="#111" stroke-width="1.5"/>
    </svg>
    <p class="abs center-x label" style="top:143px">Fire Risk Assessment</p>
    <div class="abs type-tile" style="left:69px;top:178px"><svg><use href="#ico-building"/></svg></div>
    <p class="abs label" style="left:39px;width:120px;text-align:center;top:242px">Commercial</p>
    <div class="abs type-tile" style="left:224px;top:178px"><svg><use href="#ico-house"/></svg></div>
    <p class="abs label" style="left:194px;width:120px;text-align:center;top:242px">Residential</p>

    <div class="abs section-tab" style="top:287px">Completed
      <svg viewBox="0 0 24 24"><circle cx="12" cy="13" r="9" fill="#8bc34a"/><path d="M6 13l5 5 11-14" fill="none" stroke="#1b7d2a" stroke-width="3"/></svg>
    </div>
    <div class="abs site-row" style="top:335px">
      <div class="site-chip"><svg><use href="#ico-building"/></svg></div><strong>Milo's Barbershop</strong>
    </div>

    <div class="abs section-tab" style="top:415px">In Progress<svg><use href="#ico-pie"/></svg></div>
    <div class="abs site-row" style="top:469px"><span class="ring"></span>Elm Rd School</div>
    <div class="abs site-row" style="top:498px"><span class="ring"></span>St Anne's Nursing Home</div>

    <div class="abs section-tab" style="top:549px">Purchases<svg><use href="#ico-pie"/></svg></div>
    <div class="abs site-row" style="top:603px"><span class="ring"></span>Residential Fire Risk Assessment</div>
    <div class="abs site-row" style="top:632px"><span class="ring"></span>Commercial Fire Risk Assessment</div>
    <div class="abs site-row" style="top:659px"><span class="ring"></span>Commercial Fire Risk Assessment</div>

    <nav class="tab-bar">
      <span class="tab"><svg><use href="#ico-gauge"/></svg></span>
      <span class="tab"><svg><use href="#ico-wallet"/></svg></span>
      <span class="tab"><svg fill="#111"><use href="#ico-chat"/></svg></span>
      <span class="tab"><svg><use href="#ico-exit"/></svg></span>
    </nav>
  </section>

  <section class="screen screen--support">
    <header class="app-bar"><svg fill="var(--chat)"><use href="#ico-chat"/></svg>Support</header>
    <div class="abs prompt"><span>Type / Record Your Response Here</span><svg><use href="#ico-mic"/></svg></div>
    <div class="abs reply-box"></div>
    <a class="abs send">
      <svg viewBox="0 0 30 28"><path d="M2 13L28 2 20 26l-6-9z" fill="#111"/><path d="M14 17L28 2" stroke="#fff" stroke-width="1.5"/></svg>
      Send
    </a>
    <nav class="tab-bar">
      <span class="tab"><svg><use href="#ico-gauge-dark"/></svg></span>
      <span class="tab"><svg><use href="#ico-wallet"/></svg></span>
      <span class="tab"><svg fill="var(--chat)"><use href="#ico-chat"/></svg></span>
      <span class="tab"><svg><use href="#ico-exit"/></svg></span>
    </nav>
  </section>

</main>
</body>
</html>
```